Vernac Law Business cards and stationary design project

We are looking for a stationary design for business cards (double sided), 8x10, 5x7, and legal and standard envelopes.

We would like the design to match the logo that we have already.
Color palate preferred is Teal, White, grey and any others that will look good for a professional law firm.

We would like this statement: "RELATIONSHIPS. RESPECT. RESULT" to be on the back of the business cards and maybe on the stationary if it looks good.

Please see link to website for more information: www.vernac-law.example

Target Market(s)

Potential clients that need Attorney services.

Industry/Entity Type

Law Firm

Contact Information for Business Card

We would like the front and back to be two different colors. Current business cards are teal front, grey back and are a vertical design. We are open to options with colors.

Font styles to use
Serif

Colors
33a6d7
33b8a4
b9b9b9
5c5c5c

Requirements
Must have
• Logo supplied needs to go on the card and stationary.
• Match website color palate, www.vernac-law.example
• Be professional and not too wordy.
• Criminal Law, Civil Litigation, Personal Injury, Restraining Orders need to be on the card.
Nice to have
• RELATIONSHIPS. RESPECT. RESULTS. on the back of the card.
Should not have
• Not be too busy/wordy or too flashy.

```html
<!DOCTYPE html>
<html lang="en">
<head>
<meta charset="utf-8">
<title>Vernac Law – Business Card</title>
<link rel="stylesheet" href="https://fonts.googleapis.com/css2?family=Open+Sans:wght@400;600;700&display=swap">
<style>
  :root {
    --teal: #14899a;
    --teal-dark: #0f7482;
    --ink: #3a3a3a;
    --grey: #5c5c5c;
    --card-white: #ffffff;
    --card-black: #1e1e1e;
    --card-black-light: #2c2c2c;
    --backdrop: #e4e4e2;
  }
  * { box-sizing: border-box; margin: 0; padding: 0; }
  html, body {
    width: 1200px;
    height: 900px;
    overflow: hidden;
    background: var(--backdrop);
    font-family: "Open Sans", Arial, sans-serif;
  }
  .canvas {
    position: relative;
    width: 1200px;
    height: 900px;
  }
  .card {
    position: absolute;
    left: 290px;
    width: 620px;
    height: 354px;
    overflow: hidden;
    box-shadow: 0 6px 18px rgba(0,0,0,0.18);
  }

  /* Back side */
  .card-back {
    top: 66px;
    background: linear-gradient(135deg, var(--card-black) 0%, var(--card-black-light) 45%, var(--card-black) 100%);
    color: #fff;
    text-align: center;
  }
  .card-back .wordmark {
    position: absolute;
    top: 92px;
    left: 0;
    right: 0;
    display: flex;
    justify-content: center;
    align-items: center;
    gap: 14px;
  }
  .wordmark-square {
    width: 20px;
    height: 20px;
    background: currentColor;
  }
  .wordmark-name {
    font-weight: 600;
    font-size: 36px;
    letter-spacing: 4px;
    text-transform: uppercase;
  }
  .practice-areas {
    position: absolute;
    top: 186px;
    left: 0;
    right: 0;
    font-weight: 700;
    font-size: 15px;
    line-height: 21px;
  }
  .motto {
    position: absolute;
    top: 244px;
    left: 0;
    right: 0;
    font-weight: 700;
    font-size: 15px;
    letter-spacing: 0.3px;
  }

  /* Front side */
  .card-front {
    top: 478px;
    background: var(--card-white);
    color: var(--ink);
  }
  .card-front .decor {
    position: absolute;
    inset: 0;
  }
  .person {
    position: absolute;
    top: 24px;
    left: 66px;
  }
  .person-name {
    color: var(--teal);
    font-weight: 700;
    font-size: 19px;
    line-height: 22px;
  }
  .person-title {
    color: var(--grey);
    font-size: 13px;
  }
  .contact {
    position: absolute;
    top: 126px;
    left: 24px;
    font-size: 14px;
    line-height: 18px;
    color: var(--ink);
    list-style: none;
  }
  .contact .address { margin-bottom: 8px; }
  .contact li {
    display: flex;
    align-items: center;
    gap: 6px;
  }
  .contact svg { width: 11px; height: 11px; fill: var(--teal); flex: none; }
  .card-front .wordmark {
    position: absolute;
    top: 140px;
    left: 260px;
    display: flex;
    align-items: center;
    gap: 12px;
    color: var(--teal);
  }
  .card-front .wordmark-name { font-size: 32px; }
</style>
</head>
<body>
<main class="canvas">

  <section class="card card-back" aria-label="Business card back">
    <div class="wordmark">
      <span class="wordmark-square"></span>
      <span class="wordmark-name">Vernac Law</span>
    </div>
    <p class="practice-areas">
      Practice areas, Criminal Law<br>
      Civil Litigation/Personal Injury, Restraining Orders
    </p>
    <p class="motto">RELATIONSHIPS. RESPECT. RESULT</p>
  </section>

  <section class="card card-front" aria-label="Business card front">
    <svg class="decor" width="620" height="354" viewBox="0 0 620 354" aria-hidden="true">
      <polygon points="14,20 56,20 28,52 14,52" fill="var(--teal)"/>
      <rect x="0" y="300" width="240" height="10" fill="var(--teal)"/>
      <polygon points="262,300 620,300 620,354 222,354" fill="var(--teal)"/>
    </svg>

    <div class="person">
      <p class="person-name">John Smith</p>
      <p class="person-title">Managing Director</p>
    </div>

    <ul class="contact">
      <li class="address">12345, Address Goes Here<br>Country Name, 123456</li>
      <li>
        <svg viewBox="0 0 12 12"><path d="M2 1h3l1 3-1.5 1a7 7 0 0 0 2.5 2.5L8 6l3 1v3a1 1 0 0 1-1 1A9 9 0 0 1 1 2a1 1 0 0 1 1-1z"/></svg>
        044-123 456 789
      </li>
      <li>
        <svg viewBox="0 0 12 12"><rect x="2" y="1" width="8" height="10" rx="1"/></svg>
        044-123 456 789
      </li>
      <li>
        <svg viewBox="0 0 12 12"><path d="M1 3h10v6H1z M1 3l5 4 5-4" /></svg>
        info@vernac-law.example
      </li>
    </ul>

    <div class="wordmark">
      <span class="wordmark-square"></span>
      <span class="wordmark-name">Vernac Law</span>
    </div>
  </section>

</main>
</body>
</html>
```